Stylish new business card needed!

Hello everyone! I am in need of a new business card design for an alarm company here in Hurricane WV. I have all fonts, color codes and logos provided for you use! We are a young company and like the style of a clean sleek looking business card. Would like it double sided, one side holding the logo and the other with your design!
Target Market(s)
The people that are looking for the newest tech for home automation and security
Industry/Entity Type
Alarm services; Home automation
Contact Information for Business Card
Name of person; position (Sales; Installer); Phone Number (555.418.7260); Employee cell Number; Website (www.GuardedByVelk.example); Employee Email; Double sided
Look and feel
Each slider illustrates characteristics of the customer's brand and the style your logo design should communicate.

```html
<!DOCTYPE html>
<html lang="en">
<head>
<meta charset="utf-8">
<title>Velk Business Card</title>
<link rel="stylesheet" href="https://fonts.googleapis.com/css2?family=Montserrat:wght@400;500;700&display=swap">
<style>
  :root {
    --orange: #f4914f;
    --grey: #939393;
    --ink: #333333;
    --rule: #b5b5b5;
    --card-white: #ffffff;
    --stage: #e9e9e9;
  }
  * { margin: 0; padding: 0; box-sizing: border-box; }
  html, body {
    width: 1200px;
    height: 802px;
    overflow: hidden;
    background: var(--stage);
    font-family: "Montserrat", sans-serif;
  }
  .sheet {
    width: 1200px;
    height: 802px;
    display: flex;
    align-items: center;
    justify-content: center;
    gap: 40px;
  }
  .card {
    width: 540px;
    height: 309px;
    border-radius: 22px;
    position: relative;
    overflow: hidden;
  }
  .card--front {
    background: var(--card-white);
    display: flex;
    align-items: center;
  }
  .card--back {
    background: var(--orange);
    display: flex;
    align-items: center;
    justify-content: center;
  }
  .brand {
    width: 250px;
    display: flex;
    align-items: center;
    justify-content: center;
  }
  .brand__name {
    font-weight: 500;
    letter-spacing: 4px;
    color: var(--grey);
    font-size: 58px;
    line-height: 1;
  }
  .card--back .brand__name {
    color: var(--card-white);
    font-size: 104px;
    letter-spacing: 8px;
  }
  .divider {
    width: 1px;
    height: 150px;
    background: var(--rule);
  }
  .contact {
    padding-left: 26px;
    color: var(--ink);
    font-size: 12.5px;
    line-height: 1.55;
  }
  .contact__name {
    color: var(--orange);
    font-weight: 700;
    font-size: 19px;
    letter-spacing: 0.5px;
    text-transform: uppercase;
    line-height: 1.1;
  }
  .contact__role {
    font-size: 12.5px;
    margin-bottom: 8px;
  }
  .contact__line {
    display: flex;
    align-items: center;
    gap: 7px;
  }
  .contact__icon {
    width: 10px;
    height: 10px;
    flex: none;
  }
  .contact__address {
    margin-top: 2px;
  }
</style>
</head>
<body>
  <main class="sheet">
    <section class="card card--front" aria-label="Card front">
      <div class="brand"><span class="brand__name">VELK</span></div>
      <div class="divider"></div>
      <div class="contact">
        <p class="contact__name">Daren Cole</p>
        <p class="contact__role">Sales/Installer</p>
        <p class="contact__line">
          <svg class="contact__icon" viewBox="0 0 10 10" aria-hidden="true"><path d="M2 1 L3.6 1 L4.3 3 L3.2 3.8 Q4 5.8 6.2 6.8 L7 5.7 L9 6.4 L9 8 Q8.6 9 7.5 9 Q1 8.2 1 2.5 Q1 1.2 2 1 Z" fill="var(--orange)"/></svg>
          555.418.7260
        </p>
        <p class="contact__line">
          <svg class="contact__icon" viewBox="0 0 10 10" aria-hidden="true"><rect x="0.5" y="2" width="9" height="6.5" rx="0.6" fill="var(--orange)"/><path d="M0.8 2.4 L5 5.6 L9.2 2.4" stroke="#fff" stroke-width="0.9" fill="none"/></svg>
          info@GuardedByVelk.example
        </p>
        <p class="contact__line">
          <svg class="contact__icon" viewBox="0 0 10 10" aria-hidden="true"><circle cx="5" cy="5" r="4.5" fill="var(--orange)"/><path d="M0.5 5 H9.5 M5 0.5 V9.5 M5 0.5 Q2 5 5 9.5 M5 0.5 Q8 5 5 9.5" stroke="#fff" stroke-width="0.6" fill="none"/></svg>
          www.GuardedByVelk.example
        </p>
        <p class="contact__address">1480 W Harlan Avenue<br>Ridgeview County 7402</p>
      </div>
    </section>
    <section class="card card--back" aria-label="Card back">
      <span class="brand__name">VELK</span>
    </section>
  </main>
</body>
</html>
```